VENTURE CAPITAL GROUP BUSINESS CARD DESIGN

Venture Capital Group based in SF looking for a bold business card design. No trendy colour explosion, 3D effects etc. Just "simple" optical effects. Works on your brain, keeps your eye focused and sticks to your mind.
Target Market(s)
Technology startups
Industry/Entity Type
Venture Capital
Contact Information for Business Card
DESMOND WHITLAKE
MANAGING PARTNER
187 FENWORTH ST SAN FRANCISCO, CA 94187
415.555.0142 O
415.555.0147 F
415.555.0193 C
desmond@veldtmoorcapital.ventures

```html
<!DOCTYPE html>
<html lang="en">
<head>
<meta charset="utf-8">
<title>Veldtmoor Capital Group – Business Card</title>
<link rel="stylesheet" href="https://fonts.googleapis.com/css2?family=Cinzel:wght@400;500&family=Merriweather:wght@400;700&family=Roboto+Condensed:wght@400&display=swap">
<style>
  :root {
    --stage: #a9a7a8;
    --paper: #ffffff;
    --green-deep: #0f6a35;
    --green-mid: #1f8a3e;
    --green-light: #5cbf4f;
    --silver: #b9b9b9;
    --silver-dark: #8c8c8c;
    --ink-grey: #5d5d5d;
    --orb: #ececec;
  }
  * { margin: 0; padding: 0; box-sizing: border-box; }
  html, body { width: 1200px; height: 1200px; overflow: hidden; }
  body { background: var(--stage); position: relative; }

  .card {
    position: absolute;
    left: 240px;
    width: 720px;
    height: 420px;
    background: var(--paper);
    overflow: hidden;
  }
  .card--front { top: 110px; }
  .card--back { top: 660px; }

  .orb {
    position: absolute;
    border-radius: 50%;
    background: radial-gradient(circle at 50% 45%, #fafafa 0%, var(--orb) 75%, #e1e1e1 100%);
  }
  .wordmark {
    position: absolute;
    text-align: center;
    transform: translateX(-50%);
    white-space: nowrap;
  }
  .wordmark__name {
    font-family: "Cinzel", serif;
    font-weight: 500;
    color: var(--green-mid);
    line-height: 1;
    display: block;
  }
  .wordmark__tag {
    font-family: "Cinzel", serif;
    font-weight: 400;
    color: var(--silver-dark);
    display: block;
    line-height: 1;
  }

  /* front */
  .card--front .orb { left: 278px; top: 87px; width: 162px; height: 162px; }
  .card--front .wordmark { left: 360px; top: 277px; }
  .card--front .wordmark__name { font-size: 46px; letter-spacing: 1px; }
  .card--front .wordmark__tag { font-size: 13px; letter-spacing: 5px; margin-top: 2px; }

  /* back */
  .card--back .orb { left: 100px; top: 48px; width: 158px; height: 158px; }
  .card--back .wordmark { left: 181px; top: 236px; }
  .card--back .wordmark__name { font-size: 37px; letter-spacing: 1px; }
  .card--back .wordmark__tag { font-size: 10.5px; letter-spacing: 4px; margin-top: 1px; }

  .holder {
    position: absolute;
    right: 40px;
    top: 54px;
    text-align: right;
    font-family: "Merriweather", serif;
    color: var(--ink-grey);
  }
  .holder__name { font-size: 21px; font-weight: 700; }
  .holder__title { font-size: 15px; font-weight: 400; margin-top: 4px; }

  .wave { position: absolute; left: 0; top: 0; }

  .contact {
    position: absolute;
    right: 24px;
    top: 272px;
    list-style: none;
    font-family: "Roboto Condensed", sans-serif;
    font-size: 17px;
    color: #ffffff;
  }
  .contact__item {
    display: flex;
    justify-content: flex-end;
    align-items: center;
    height: 24.5px;
    gap: 14px;
  }
  .contact__icon { width: 18px; height: 18px; flex: none; }
</style>
</head>
<body>

<section class="card card--front" aria-label="Card front">
  <div class="orb"></div>
  <div class="wordmark">
    <span class="wordmark__name">Veldtmoor</span>
    <span class="wordmark__tag">Capital Group</span>
  </div>
</section>

<section class="card card--back" aria-label="Card back">
  <svg class="wave" width="720" height="420" viewBox="0 0 720 420">
    <defs>
      <linearGradient id="band-green" x1="0" y1="0" x2="1" y2="0">
        <stop offset="0" stop-color="var(--green-light)"/>
        <stop offset="0.45" stop-color="var(--green-mid)"/>
        <stop offset="1" stop-color="var(--green-deep)"/>
      </linearGradient>
      <linearGradient id="band-silver" x1="0" y1="0" x2="1" y2="0">
        <stop offset="0" stop-color="#d6d6d6"/>
        <stop offset="0.5" stop-color="var(--silver)"/>
        <stop offset="1" stop-color="var(--silver-dark)"/>
      </linearGradient>
    </defs>
    <path d="M0,338 C140,362 300,378 440,300 C540,244 630,208 720,200 L720,216 C630,224 545,258 450,312 C310,392 140,382 0,362 Z" fill="url(#band-silver)"/>
    <path d="M30,356 C180,374 320,364 420,318" fill="none" stroke="#cfcfcf" stroke-width="3"/>
    <path d="M0,388 C160,386 330,372 450,306 C550,252 640,228 720,224 L720,420 L0,420 Z" fill="url(#band-green)"/>
  </svg>

  <div class="orb"></div>
  <div class="wordmark">
    <span class="wordmark__name">Veldtmoor</span>
    <span class="wordmark__tag">Capital Group</span>
  </div>

  <div class="holder">
    <p class="holder__name">Desmond Whitlake</p>
    <p class="holder__title">Managing Partner</p>
  </div>

  <ul class="contact">
    <li class="contact__item"><span>415.555.0142</span>
      <svg class="contact__icon" viewBox="0 0 20 20" aria-hidden="true"><path d="M2 7 C2 3 18 3 18 7 L15 9 L13 7 L7 7 L5 9 Z" fill="#fff"/><rect x="5" y="10" width="10" height="7" rx="1.5" fill="#fff"/></svg></li>
    <li class="contact__item"><span>415.555.0147</span>
      <svg class="contact__icon" viewBox="0 0 20 20" aria-hidden="true"><rect x="5" y="2" width="10" height="5" fill="#fff"/><rect x="2" y="8" width="16" height="7" rx="1.5" fill="#fff"/><rect x="5" y="13" width="10" height="5" fill="#fff" stroke="var(--green-deep)" stroke-width="1"/></svg></li>
    <li class="contact__item"><span>415.555.0193</span>
      <svg class="contact__icon" viewBox="0 0 20 20" aria-hidden="true"><rect x="5" y="1" width="10" height="18" rx="2" fill="#fff"/><rect x="7" y="4" width="6" height="10" fill="var(--green-deep)"/></svg></li>
    <li class="contact__item"><span>desmond@veldtmoorcapital.ventures</span>
      <svg class="contact__icon" viewBox="0 0 20 20" aria-hidden="true"><rect x="1" y="4" width="18" height="12" fill="#fff"/><path d="M1 4 L10 11 L19 4" fill="none" stroke="var(--green-deep)" stroke-width="1.3"/></svg></li>
    <li class="contact__item"><span>187 Fenworth St San Francisco, CA 94187</span>
      <svg class="contact__icon" viewBox="0 0 20 20" aria-hidden="true"><circle cx="10" cy="10" r="8.5" fill="#fff"/><g fill="none" stroke="var(--green-deep)" stroke-width="1"><ellipse cx="10" cy="10" rx="3.5" ry="8.5"/><line x1="1.5" y1="10" x2="18.5" y2="10"/><line x1="10" y1="1.5" x2="10" y2="18.5"/><path d="M3 6 H17 M3 14 H17"/></g></svg></li>
  </ul>
</section>

</body>
</html>
```